Business Card Design Project

I need a business card designed that is clean, simple and elegant.
I am a fashion and advertising photographer based in Cape Town and Durban South Africa.
check out my website: www.marekvollan.co.za for ideas
Updates
Hi all,
Thanks for your submissions so far!
Please note:
I want no more than than black, white and/or grey to be used.
I don't want any photos used.
I would like the card to be double sided.
I would like to continue the design similar to the past ones Ive used.
I hope this helps, please send me further questions should you have any.
many thanks!
Marek
Hi,
Please have a look at the jpg I loaded(called inspiration) which is the direction or inspiration I am aiming at.
Also PLEASE remember NO PHOTOS to be included on the card
many thanks!!
Target Market(s)
You can look at my site to get a better understanding of the audience:
www.marekvollan.co.za
Industry/Entity Type
Advertising
Requirements
Must have
- Clean design which can also be used for a watermark on photographs
perhaps black background with white text/grey
company called: Marek Vollan Photography
Nice to have
- below I have added logos that I have used in the past.
Should not have
- pictures of cameras
tacky elements

```html
<!DOCTYPE html>
<html lang="en">
<head>
<meta charset="utf-8">
<title>Marek Vollan Photography – Business Card</title>
<link rel="stylesheet" href="https://fonts.googleapis.com/css2?family=Josefin+Sans:wght@300;400&display=swap">
<style>
  :root {
    --page: #ffffff;
    --card: #000000;
    --ink: #c4c4c4;
    --ink-soft: #a8a8a8;
    --photo-dark: #080808;
    --photo-mid: #3d3d3d;
    --photo-light: #9a9a9a;
  }
  html, body {
    margin: 0;
    width: 1200px;
    height: 900px;
    overflow: hidden;
    background: var(--page);
  }
  .canvas {
    position: relative;
    width: 1200px;
    height: 900px;
    background: var(--page);
  }
  .card {
    position: absolute;
    left: 16px;
    top: 136px;
    width: 1168px;
    height: 648px;
    background: var(--card);
    overflow: hidden;
    font-family: "Josefin Sans", "Century Gothic", sans-serif;
    color: var(--ink);
  }
  .brand {
    margin: 0;
    font-weight: 300;
  }
  .brand__line {
    position: absolute;
    white-space: nowrap;
    line-height: 1;
    text-transform: uppercase;
  }
  .brand__first,
  .brand__last {
    font-size: 134px;
    font-weight: 300;
    letter-spacing: 0;
  }
  .brand__first {
    left: 360px;
    top: 84px;
    transform: translateX(-50%) scaleX(0.85);
  }
  .brand__last {
    left: 310px;
    top: 184px;
    transform: translateX(-50%) scaleX(0.85);
  }
  .brand__trade {
    left: 353px;
    top: 300px;
    transform: translateX(-50%);
    font-size: 33px;
    font-weight: 400;
    letter-spacing: 0.03em;
  }
  .contact {
    position: absolute;
    left: 350px;
    top: 423px;
    transform: translateX(-50%);
    margin: 0;
    padding: 0;
    list-style: none;
    text-align: center;
    font-size: 27px;
    font-weight: 300;
    line-height: 46px;
    color: var(--ink-soft);
    white-space: nowrap;
  }
  .portrait {
    position: absolute;
    left: 640px;
    top: 0;
    width: 528px;
    height: 648px;
    background:
      radial-gradient(ellipse 38% 30% at 40% 30%, var(--photo-light) 0%, var(--photo-mid) 45%, transparent 80%),
      radial-gradient(ellipse 34% 28% at 66% 50%, var(--photo-mid) 0%, transparent 75%),
      linear-gradient(90deg, var(--card) 0%, var(--photo-dark) 30%, var(--photo-dark) 100%);
  }
</style>
</head>
<body>
  <div class="canvas">
    <section class="card">
      <h1 class="brand">
        <span class="brand__line brand__first">Marek</span>
        <span class="brand__line brand__last">Vollan</span>
        <span class="brand__line brand__trade">Photography</span>
      </h1>
      <ul class="contact">
        <li class="contact__email">marek@marekvollan.co.za</li>
        <li class="contact__mobile">+27 (0)82 555 0147</li>
        <li class="contact__office">+27 (0)31 555 0192</li>
      </ul>
      <div class="portrait" role="img" aria-label="Dramatic low-key fashion photograph of two models posed against a black background"></div>
    </section>
  </div>
</body>
</html>
```